Pitch Orchard

We need a logo and website that reflects a platform, enabling for users (consultants and corporate clients) to have for them powerpoint slides produced.
See the mockup in attachment - Look& feel Style www.brintova.com. See a similar website content (but outdated presentation and to be made more appealing with new modern ways to promote (old website with same proposition: http://www.yondercraftpanel.com/). Look and feel wished: www.glantirex.com (see number that show dynamic evolution) or www.brintova.com

We have no name - that is part of the mission

```html
<!DOCTYPE html>
<html lang="en">
<head>
<meta charset="utf-8">
<title>Deckwise Visual — Cost / Speed / Quality</title>
<link href="https://fonts.googleapis.com/css2?family=Oswald:wght@300;400;500&family=Open+Sans:wght@400;600;700&display=swap" rel="stylesheet">
<style>
:root{
  --blue:#1f7fd6;
  --blue-deep:#155fa8;
  --blue-hero-1:#2a6fb8;
  --blue-hero-2:#8fb7dd;
  --orange:#f28c1e;
  --dark:#3d3d3f;
  --ink:#333;
  --muted:#777;
  --line:#dedede;
  --paper:#fff;
  --footer:#f1f1f1;
  --bottom:#e4e4e4;
}
*{box-sizing:border-box;margin:0;padding:0}
html,body{width:1200px;height:2524px;overflow:hidden}
body{font-family:"Open Sans",Arial,sans-serif;color:var(--ink);background:var(--paper)}
.heading{font-family:"Oswald",Arial,sans-serif;font-weight:400;text-transform:uppercase;color:var(--ink);font-size:30px;letter-spacing:.5px}

/* Hero */
.hero{position:relative;height:600px;overflow:hidden}
.hero-photo{position:absolute;inset:0;background:linear-gradient(160deg,var(--blue-hero-1) 0%,#4f8fcb 45%,var(--blue-hero-2) 100%)}
.hero-photo::after{content:"";position:absolute;inset:0;background:rgba(20,80,150,.35)}
.site-header{position:absolute;top:0;left:0;right:0;height:70px;display:flex;align-items:center;justify-content:space-between;padding:0 60px 0 50px;z-index:2}
.brand{display:flex;align-items:center;gap:10px;color:#fff}
.brand-mark{width:34px;height:34px;background:#fff;border-radius:4px}
.brand-name{font-family:"Open Sans",sans-serif;font-weight:700;font-size:20px;line-height:1}
.brand-tag{font-size:10px;opacity:.85;display:block;margin-top:3px;font-weight:400}
.main-nav{display:flex;align-items:center;gap:28px;font-size:12px;font-weight:600;color:#fff;text-transform:uppercase}
.nav-cta{background:var(--orange);padding:10px 16px;border-radius:2px}
.hero-title{position:absolute;top:296px;left:0;right:0;text-align:center;font-family:"Oswald",sans-serif;font-weight:400;font-size:74px;color:#fff;z-index:2}
.hero-dots{position:absolute;top:400px;left:0;right:0;display:flex;justify-content:center;gap:10px;z-index:2}
.hero-dots span{width:12px;height:12px;border-radius:50%;border:2px solid #fff}
.hero-dots span.active{background:#fff}

/* Stats */
.stats{height:110px;background:var(--dark);display:flex;justify-content:space-around;align-items:center;padding:0 80px;color:#fff;text-align:center}
.stat-value{font-family:"Oswald",sans-serif;font-size:28px;font-weight:400;display:block}
.stat-label{font-size:12px;color:#ccc}

/* Clients */
.clients{height:230px;text-align:center;padding-top:50px}
.client-row{display:flex;justify-content:center;gap:22px;margin-top:30px}
.client{width:150px;height:60px;border:1px solid var(--line);display:flex;align-items:center;justify-content:center;font-family:"Oswald",sans-serif;font-size:20px;color:#8a8a8a;text-transform:uppercase}

/* Value */
.value{height:420px;position:relative;padding:55px 0 0 100px}
.value-text{width:460px}
.value-text .heading{margin-bottom:22px}
.value-text p{font-size:12px;line-height:1.75;color:var(--muted);margin-bottom:16px}
.slide-shot{position:absolute;background:linear-gradient(135deg,#f4f4f4,#dcdcdc);border:1px solid #bbb}
.shot-before{left:700px;top:110px;width:300px;height:200px}
.shot-after{left:800px;top:40px;width:330px;height:210px}
.tag{position:absolute;font-size:14px;color:var(--blue);border:1px solid var(--blue);background:#fff;padding:4px 14px}
.tag-before{left:800px;top:325px}
.tag-after{left:1060px;top:10px}

/* Gallery */
.gallery{height:400px;background:linear-gradient(180deg,var(--blue) 0%,var(--blue-deep) 100%);text-align:center;padding-top:50px}
.gallery .heading{color:#fff}
.gallery-row{display:flex;justify-content:center;gap:70px;margin-top:40px}
.gallery-card{width:360px;height:220px;background:#fff;padding:14px;text-align:left}
.card-title{font-size:11px;font-weight:700;color:var(--ink);text-transform:uppercase}
.card-sub{font-size:10px;color:var(--muted);margin:2px 0 10px}
.card-chart{height:150px;background:linear-gradient(180deg,#f3e3e3,#e9c9c9)}

/* Services */
.services{height:380px;display:flex;justify-content:center;gap:160px;padding-top:60px;text-align:center}
.service{width:380px}
.service-icon{width:90px;height:90px;border-radius:50%;background:var(--blue);margin:0 auto 18px;display:flex;align-items:center;justify-content:center}
.service h3{font-family:"Oswald",sans-serif;font-weight:400;font-size:24px;color:var(--blue);margin-bottom:12px}
.service p{font-size:12px;line-height:1.7;color:var(--muted)}
.read-more{display:inline-block;margin-top:12px;font-size:13px;color:var(--ink)}

/* Footer */
.site-footer{height:340px;background:var(--footer);display:flex;gap:50px;padding:55px 60px 0 90px}
.footer-col{width:230px;font-size:12px;color:var(--muted);line-height:1.7}
.footer-col h4{font-size:13px;font-weight:700;color:var(--ink);text-transform:uppercase;margin-bottom:14px}
.footer-brand .brand{color:var(--blue-deep);margin-bottom:16px}
.footer-brand .brand-mark{background:var(--blue-deep)}
.social{display:flex;gap:8px;margin-top:16px}
.social span{width:26px;height:26px;border-radius:50%;background:var(--blue-deep)}
.news-input{width:220px;height:34px;border:1px solid #ccc;background:#fff;margin:14px 0 10px;padding:0 10px;font-size:11px;line-height:32px;color:#aaa}
.news-btn{display:inline-block;background:var(--blue);color:#fff;font-size:11px;padding:8px 14px;text-transform:uppercase}
.contact-line{display:flex;gap:10px;align-items:flex-start;margin-bottom:12px}
.contact-line svg{flex:none;margin-top:3px}
.quick-links{list-style:none}
.quick-links li{margin-bottom:6px}
.bottom-bar{height:44px;background:var(--bottom);text-align:center;font-size:11px;color:var(--muted);line-height:44px}
</style>
</head>
<body>

<section class="hero">
  <div class="hero-photo" role="img" aria-label="Photo of a team meeting around a conference table with a presenter at a screen, tinted blue"></div>
  <header class="site-header">
    <div class="brand"><span class="brand-mark"></span><span class="brand-name">Deckwise Visual<span class="brand-tag">clear slides for every proposition</span></span></div>
    <nav class="main-nav">
      <span>Our value proposition</span><span>Who we are</span><span>Pricing</span><span>Contact</span><span class="nav-cta">Registration</span>
    </nav>
  </header>
  <h1 class="hero-title">Cost/Speed/Quality</h1>
  <div class="hero-dots"><span class="active"></span><span></span></div>
</section>

<section class="stats">
  <div><span class="stat-value">12</span><span class="stat-label">Countries active</span></div>
  <div><span class="stat-value">145</span><span class="stat-label">Corporate Clients served</span></div>
  <div><span class="stat-value">20.000</span><span class="stat-label">Slides produced</span></div>
  <div><span class="stat-value">1540</span><span class="stat-label">Free-lance consultants served</span></div>
</section>

<section class="clients">
  <h2 class="heading">Our Clients</h2>
  <div class="client-row">
    <div class="client">Kestrel</div><div class="client">Aurelan</div><div class="client">Dipsen</div>
    <div class="client">Qorvane</div><div class="client">Brackwell</div><div class="client">Fowlmere</div>
  </div>
</section>

<section class="value">
  <div class="value-text">
    <h2 class="heading">Our Value Proposition</h2>
    <p>The main objective of Deckwise Visual is to help consultants and corporate teams turn rough drafts into polished slides. Our offshore studio delivers consistent, high-quality presentation work at a fraction of the usual cost, with short turnaround times and dedicated account managers who know your style.</p>
    <p>Leveraging our trained designers and proven templates, we help you focus on your message while we take care of layout, charts and visual clarity. Send a sketch in the evening and receive finished slides in the morning, ready to present.</p>
  </div>
  <div class="slide-shot shot-after" role="img" aria-label="Redesigned slide example after formatting"></div>
  <div class="slide-shot shot-before" role="img" aria-label="Hand-sketched draft slide before formatting"></div>
  <span class="tag tag-before">Before</span>
  <span class="tag tag-after">After</span>
</section>

<section class="gallery">
  <h2 class="heading">Gallery of Finished Work</h2>
  <div class="gallery-row">
    <div class="gallery-card">
      <div class="card-title">Private equity industry</div>
      <div class="card-sub">Operational value creation overview</div>
      <div class="card-chart" role="img" aria-label="Slide with a bar chart of fund returns"></div>
    </div>
    <div class="gallery-card">
      <div class="card-title">Private equity industry</div>
      <div class="card-sub">Operational value creation levers</div>
      <div class="card-chart" role="img" aria-label="Slide with a table of value creation levers"></div>
    </div>
  </div>
</section>

<section class="services">
  <div class="service">
    <div class="service-icon">
      <svg width="44" height="44" viewBox="0 0 44 44" fill="none" stroke="#fff" stroke-width="3" stroke-linecap="round" stroke-linejoin="round"><path d="M8 12h28v20H8z"/><path d="M16 38h12M22 32v6"/></svg>
    </div>
    <h3>Ad hoc support</h3>
    <p>Request slide work whenever you need it, with no commitment. Upload your draft, choose a deadline and get professional slides back on time, every time.</p>
    <span class="read-more">Read More &rsaquo;</span>
  </div>
  <div class="service">
    <div class="service-icon">
      <svg width="44" height="44" viewBox="0 0 44 44" fill="none" stroke="#fff" stroke-width="3" stroke-linecap="round" stroke-linejoin="round"><circle cx="22" cy="22" r="15"/><path d="M15 22l5 5 9-10"/></svg>
    </div>
    <h3>Dedicated support</h3>
    <p>When your volume is regular, a dedicated designer joins your team, learns your templates and style, and delivers steady output for each of your projects.</p>
    <span class="read-more">Read More &rsaquo;</span>
  </div>
</section>

<footer class="site-footer">
  <div class="footer-col footer-brand">
    <div class="brand"><span class="brand-mark"></span><span class="brand-name">Deckwise Visual</span></div>
    <p>We turn proposals, pitch and client decks into sharp presentations that win attention and save your team hours.</p>
    <div class="social"><span></span><span></span><span></span></div>
  </div>
  <div class="footer-col">
    <h4>Sign up for newsletter</h4>
    <p>Templates and practical tips on slide design, sent once a month.</p>
    <div class="news-input">Enter email</div>
    <span class="news-btn">Subscribe</span>
  </div>
  <div class="footer-col">
    <h4>Contact us</h4>
    <div class="contact-line">
      <svg width="12" height="14" viewBox="0 0 12 16"><path d="M6 0a6 6 0 0 0-6 6c0 4.5 6 10 6 10s6-5.5 6-10a6 6 0 0 0-6-6zm0 8.5A2.5 2.5 0 1 1 6 3.5a2.5 2.5 0 0 1 0 5z" fill="var(--blue)"/></svg>
      <span>Deckwise Visual Studio Ltd, 24 Harbor Row, Lakeview</span>
    </div>
    <div class="contact-line">
      <svg width="12" height="12" viewBox="0 0 16 16"><path d="M3 1l3 3-2 2c1 2 3 4 6 6l2-2 3 3-2 3C7 15 1 9 1 3z" fill="var(--blue)"/></svg>
      <span>+1 555 0142 880</span>
    </div>
    <div class="contact-line">
      <svg width="13" height="10" viewBox="0 0 16 12"><rect x="0.5" y="0.5" width="15" height="11" fill="none" stroke="var(--blue)"/><path d="M1 1l7 6 7-6" fill="none" stroke="var(--blue)"/></svg>
      <span>hello@deckwisevisual.example</span>
    </div>
  </div>
  <div class="footer-col">
    <h4>Quick links</h4>
    <ul class="quick-links"><li>Home</li><li>About Us</li><li>Our services</li><li>Pricing</li><li>Blog</li><li>Contact Us</li></ul>
  </div>
</footer>
<div class="bottom-bar">&copy;2015 - 2016 Deckwise Visual Studio Ltd. All Rights Reserved</div>

</body>
</html>
```